Wordpress Design Project for Employee Communications Site

We need a Wordpress design for a company that strategizes on and produces materials for employee communications. Improving employee communications at all levels of an organization can help improve overall company performance and results. The site needs to look very clean and professional; we're not afraid of white space. We like the functionality that Wordpress provides; however, we only want one "true" blog page; the other pages should give the impression of a more "static" web site - particularly the home page. I have a logo that I can provide.

I have added these comments to the discussion page:
Great question - thank you for asking it. I’ve done more research

I like the very clean and monochromatic looks to many of these. I don’t have to have monochromatic, but I do like minimal colors. Simple, clean, organized. The home page should “fit” almost entirely without scrolling. I do like fat footers that you can scroll down to. I don’t want a colored background, but any that I’ve chosen with colored backgrounds could be switched to a white background.

http://www.mirabelquennet.example/
http://pondraft.example/
http://v1.samplumworth.example/
http://howdythegoat.example/
http://stayingbrisk.example/
http://www.interiors.kelmun.example/
http://trelvmasters.example/

These last two are more corporate sites. The first one is from a well-respected consultant in my area who does a lot of what I do. And I think Harwenby does a nice job with their site. So, I want to marry the look I like with getting the content job done.

http://www.messagefuelbox.example/
http://www.harwenby.example/view/en_US/us/index.htm

Target Market(s)

Target market is mid- to large-sized companies. More than 500 employees.

Industry/Entity Type

Communications

Requirements
Must have
• Need an impactful home page. There should be a "blog" page; contact us; services; about. For starters, at least. I want fonts to be very readable - that is, either quite dark gray or black.
Nice to have
• I am loathe to include a picture of myself, but I do want some images that say, "professional" and "expert" in communications.
Should not have
• I don't want a hits counter :) (I know no one would do that!).

```html
<!DOCTYPE html>
<html lang="en">
<head>
<meta charset="utf-8">
<title>WDG – Workplace Dialogue Group</title>
<link href="https://fonts.googleapis.com/css2?family=Open+Sans:wght@400;600;700&family=Yanone+Kaffeesatz:wght@400;600&family=Ubuntu:wght@400&display=swap" rel="stylesheet">
<style>
:root{
  --lime:#c0d83a;
  --sky:#6cc3ea;
  --ink:#333333;
  --body:#444444;
  --nav:#8f8f8f;
  --rule:#e2e2e2;
  --stripe:#f1f1f1;
  --white:#ffffff;
}
*{margin:0;padding:0;box-sizing:border-box}
html,body{width:1200px;height:1100px;overflow:hidden;background:var(--white)}
body{position:relative;font-family:"Open Sans",Arial,sans-serif;color:var(--body)}
.top-bar{position:absolute;left:0;top:0;width:1200px;height:10px;background:var(--lime)}
.stripes{position:absolute;left:845px;top:10px}
.brand{position:absolute;left:216px;top:46px;display:flex;align-items:center;gap:14px}
.brand-dot{width:58px;height:58px;border-radius:50%;background:var(--sky)}
.brand-name{font-family:"Ubuntu",sans-serif;color:var(--lime);font-size:60px;line-height:1;font-weight:400}
.brand-tag{position:absolute;left:220px;top:113px;font-family:"Ubuntu",sans-serif;font-size:14px;color:#4a3f86;white-space:nowrap}
.main-nav{position:absolute;left:444px;top:161px;width:567px;height:46px;border:1px solid var(--rule);border-bottom:none}
.main-nav a{position:absolute;top:16px;font-weight:700;font-size:14px;line-height:18px;color:var(--nav);text-decoration:none;letter-spacing:.1px;white-space:nowrap}
.main-nav a.active{color:var(--sky)}
.main-nav a.active::after{content:"";position:absolute;left:-7px;right:-7px;top:27px;height:3px;background:var(--sky)}
.hero-shadow{position:absolute;left:100px;top:560px;width:1010px;height:70px;background:radial-gradient(ellipse at center top,rgba(0,0,0,.28),rgba(0,0,0,0) 70%)}
.hero-photo{position:absolute;left:210px;top:207px;width:800px;height:392px;background:linear-gradient(100deg,#e9ecef 0%,#c9ccd2 30%,#b8bec6 50%,#8a8f98 62%,#d9dde2 80%,#a8adb5 100%)}
.hero-caption{position:absolute;left:210px;top:461px;width:306px;height:111px;background:var(--sky);border-radius:0 10px 10px 0;padding:14px 19px}
.hero-caption h2{font-family:"Yanone Kaffeesatz",sans-serif;font-weight:400;font-size:32px;color:#1e2a33;line-height:1;margin-bottom:10px;white-space:nowrap}
.hero-caption p{font-family:"Ubuntu",sans-serif;font-size:15px;line-height:20px;color:#2f3a44}
.slide-arrow{position:absolute;top:364px}
.slide-dots{position:absolute;left:580px;top:610px;display:flex;gap:5px}
.slide-dots span{width:13px;height:13px;border-radius:50%;background:#9a9a9a}
.slide-dots span.current{background:var(--sky)}
.feature{position:absolute;width:227px}
.feature h3{font-family:"Yanone Kaffeesatz",sans-serif;font-weight:600;font-size:23px;color:var(--ink);line-height:1;margin-bottom:8px;white-space:nowrap}
.feature p{font-size:11px;line-height:15.7px;letter-spacing:.15px;text-align:justify;color:var(--body)}
.read-more{display:flex;align-items:center;gap:5px;margin-top:11px;font-size:11.5px;font-weight:700;color:var(--ink);text-decoration:none}
.read-more i{width:20px;height:13px;border-radius:7px;background:var(--sky);display:block}
.attribution{text-align:right;font-size:11px;font-weight:700;line-height:14.5px;color:var(--ink);margin-top:9px;padding-right:5px;letter-spacing:.2px}
.divider{position:absolute;width:1px;background:linear-gradient(var(--white),#e4e4e4 20%,#e4e4e4 80%,var(--white))}
.footer-rule{position:absolute;left:80px;top:1038px;width:1000px;height:12px;background:radial-gradient(ellipse at center top,rgba(0,0,0,.22),rgba(0,0,0,0) 70%)}
.footer-brand{position:absolute;left:202px;top:1054px;display:flex;align-items:center;gap:6px;font-family:"Ubuntu",sans-serif;font-size:26px;color:#9a9a9a}
.footer-brand span.dot{width:22px;height:22px;border-radius:50%;background:#a9a9a9}
.footer-nav{position:absolute;left:424px;top:1051px;font-size:12.5px;color:var(--ink);white-space:nowrap}
.footer-nav a{color:var(--ink);text-decoration:none}
.footer-nav .sep{margin:0 14px}
.copyright{position:absolute;left:441px;top:1081px;font-family:Arial,sans-serif;font-size:10.5px;color:var(--ink);white-space:nowrap}
.social{position:absolute;left:904px;top:1048px;display:flex;gap:2px}
.social span{width:33px;height:33px;border-radius:50%}
.social .one{background:var(--sky)}
.social .two{background:var(--lime)}
</style>
</head>
<body>
<div class="top-bar"></div>
<svg class="stripes" width="170" height="150" viewBox="0 0 170 150" aria-hidden="true">
  <polygon points="58,0 108,0 50,150 0,150" fill="var(--stripe)"/>
  <polygon points="118,0 168,0 110,150 60,150" fill="var(--stripe)"/>
</svg>

<header>
  <div class="brand"><span class="brand-dot"></span><span class="brand-name">WDG</span></div>
  <div class="brand-tag">Workplace Dialogue Group</div>
  <nav class="main-nav">
    <a class="active" href="#" style="left:29px">HOME</a>
    <a href="#" style="left:129px">ABOUT</a>
    <a href="#" style="left:242px">SERVICES</a>
    <a href="#" style="left:375px">BLOG</a>
    <a href="#" style="left:472px">CONTACT US</a>
  </nav>
</header>

<section class="hero">
  <div class="hero-shadow"></div>
  <div class="hero-photo" role="img" aria-label="Photo of a smiling businesswoman in the foreground with colleagues meeting at a table behind her"></div>
  <div class="hero-caption">
    <h2>Effective Communication</h2>
    <p>Effective communication in the work-place is the backbone of any business.</p>
  </div>
  <svg class="slide-arrow" style="left:130px" width="36" height="42" viewBox="0 0 36 42" aria-label="Previous slide"><polygon points="22,0 36,0 15,21 36,42 22,42 0,21" fill="var(--lime)"/></svg>
  <svg class="slide-arrow" style="left:1040px" width="36" height="42" viewBox="0 0 36 42" aria-label="Next slide"><polygon points="0,0 14,0 36,21 14,42 0,42 21,21" fill="var(--lime)"/></svg>
  <div class="slide-dots"><span class="current"></span><span></span><span></span><span></span></div>
</section>

<main>
  <div class="divider" style="left:461px;top:672px;height:135px"></div>
  <div class="divider" style="left:738px;top:672px;height:135px"></div>
  <div class="divider" style="left:461px;top:865px;height:135px"></div>
  <div class="divider" style="left:740px;top:865px;height:135px"></div>

  <article class="feature" style="left:209px;top:657px">
    <h3>External Communication</h3>
    <p>Effective communication in the work-place is the backbone of any business. Without it, you could miss out on important opportunities, waste time and cause your employees and custom-ers to become frustrated.</p>
    <a class="read-more" href="#"><i></i>Read More</a>
  </article>
  <article class="feature" style="left:488px;top:657px">
    <h3>Business Growth</h3>
    <p>Effective communication in the work-place is the backbone of any business. Without it, you could miss out on important opportunities, waste time and cause your employees and custom-ers to become frustrated.</p>
    <a class="read-more" href="#"><i></i>Read More</a>
  </article>
  <article class="feature" style="left:764px;top:657px">
    <h3>Internal Communication</h3>
    <p>Effective communication in the work-place is the backbone of any business. Without it, you could miss out on important opportunities, waste time and cause your employees and custom-ers to become frustrated.</p>
    <a class="read-more" href="#"><i></i>Read More</a>
  </article>

  <article class="feature" style="left:209px;top:853px">
    <h3>What Customers are Saying...</h3>
    <p>WDG is a great benchmarking tool."The WDG channels offer a very effective way to communicate with geographi-cally distributed stores and in a retail environment."</p>
    <div class="attribution">Marisol Quendry<br>Internal Communications<br>Manager</div>
  </article>
  <article class="feature" style="left:488px;top:853px">
    <h3>Internal Social Media</h3>
    <p>WDG is a great benchmarking tool."The WDG channels offer a very effective way to communicate with geographi-cally distributed stores and in a retail environment."</p>
    <div class="attribution">Specifically for employee<br>communication</div>
  </article>
  <article class="feature" style="left:765px;top:853px">
    <h3>Business Growth</h3>
    <p>WDG is a great benchmarking tool."The WDG channels offer a very effective way to communicate with geographi-cally distributed stores and in a retail environment."</p>
    <div class="attribution">Specifically for employee<br>communication</div>
  </article>
</main>

<footer>
  <div class="footer-rule"></div>
  <div class="footer-brand"><span class="dot"></span>WDG</div>
  <nav class="footer-nav">
    <a href="#">Home</a><span class="sep">|</span><a href="#">About</a><span class="sep">|</span><a href="#">Services</a><span class="sep">|</span><a href="#">Blog</a><span class="sep">|</span><a href="#">Contact Us</a>
  </nav>
  <div class="copyright">All rights reserved. © Workplace Dialogue Group 2008</div>
  <div class="social"><span class="one"></span><span class="two"></span></div>
</footer>
</body>
</html>
```